Small Business Broker Business Card Design

A business card design for a small business brokerage, which is a financial service, not unlike real estate brokerage, but for small businesses such as laundromats, pizza shops, restaurants, cleaners etc. The designs should all be simple, more conservative in nature, using the colors and font of the logo. Again, think real estate Brokerage as a business context
Contact Information for Business Card
Name: Glen R. Harlow. Title: Small Business Advisor. Email: g.harlow@bayfieldcapitalworks.example. Mobile: (555) 274-3918. Office: (555) 806-2147. www.bayfieldcapitalworks.example

```html
<!DOCTYPE html>
<html lang="en">
<head>
<meta charset="utf-8">
<title>Bayfield Capital Works – Business Card</title>
<link rel="stylesheet" href="https://fonts.googleapis.com/css2?family=Montserrat:wght@600;700&family=Open+Sans:wght@400;700&display=swap">
<style>
  :root {
    --navy: #1a3966;
    --green: #8dc63f;
    --white: #ffffff;
    --rule: #b5b5b5;
    --backdrop: #9a9a9a;
  }
  html, body {
    margin: 0;
    width: 1200px;
    height: 1200px;
    overflow: hidden;
    background: var(--backdrop);
  }
  .card {
    position: absolute;
    left: 226px;
    width: 746px;
    height: 436px;
  }
  .card--front { top: 141px; background: var(--navy); }
  .card--back  { top: 659px; background: var(--white); }

  /* Front brand line */
  .front-brand {
    position: absolute;
    left: 0; right: 0; top: 50%;
    transform: translateY(-50%);
    display: flex;
    justify-content: center;
    align-items: center;
    gap: 16px;
  }
  .brand-square {
    width: 32px; height: 32px;
    background: var(--green);
    flex: none;
  }
  .brand-name {
    font-family: "Montserrat", sans-serif;
    font-weight: 600;
    text-transform: uppercase;
    margin: 0;
    line-height: 1;
  }
  .front-brand .brand-name { color: var(--white); font-size: 26px; }
  .tagline {
    font-family: "Montserrat", sans-serif;
    font-weight: 700;
    color: var(--green);
    text-transform: uppercase;
    margin: 6px 0 0;
    line-height: 1;
    white-space: nowrap;
  }
  .front-brand .tagline { font-size: 12px; letter-spacing: 1.2px; }

  /* Back brand block */
  .back-brand {
    position: absolute;
    left: 0; width: 343px;
    top: 168px;
    text-align: center;
  }
  .back-brand .brand-square {
    margin: 0 auto 22px;
    width: 44px; height: 44px;
    background: var(--navy);
  }
  .back-brand .brand-name { color: var(--navy); font-size: 15px; }
  .back-brand .tagline { font-size: 8.5px; letter-spacing: 0.9px; margin-top: 5px; }

  .divider {
    position: absolute;
    left: 343px; top: 141px;
    width: 1px; height: 207px;
    background: var(--rule);
  }

  /* Contact block */
  .contact {
    position: absolute;
    left: 370px; top: 147px;
    font-family: "Open Sans", sans-serif;
    color: var(--navy);
  }
  .person-name {
    font-family: "Montserrat", sans-serif;
    font-weight: 700;
    font-size: 23px;
    text-transform: uppercase;
    margin: 0;
    line-height: 1;
  }
  .person-title {
    font-family: "Montserrat", sans-serif;
    font-weight: 700;
    font-size: 12.5px;
    letter-spacing: 0.6px;
    color: var(--green);
    text-transform: uppercase;
    margin: 6px 0 0;
  }
  .details {
    list-style: none;
    margin: 26px 0 0;
    padding: 0;
    font-size: 16.5px;
    line-height: 25.5px;
  }
  .details .label { color: var(--green); font-weight: 700; }
  .website {
    margin: 47px 0 0;
    font-size: 17px;
  }
  .website strong { font-weight: 700; }
</style>
</head>
<body>
  <section class="card card--front">
    <div class="front-brand">
      <span class="brand-square"></span>
      <div>
        <p class="brand-name">Bayfield Capital Works, Inc</p>
        <p class="tagline">Sound advice for every main street business deal</p>
      </div>
    </div>
  </section>

  <section class="card card--back">
    <div class="back-brand">
      <div class="brand-square"></div>
      <p class="brand-name">Bayfield Capital Works, Inc</p>
      <p class="tagline">Sound advice for every main street business deal</p>
    </div>

    <div class="divider"></div>

    <div class="contact">
      <h1 class="person-name">Glen R. Harlow</h1>
      <p class="person-title">Small Business Advisor</p>
      <ul class="details">
        <li><span class="label">e:</span> g.harlow@bayfieldcapitalworks.example</li>
        <li><span class="label">m:</span> (555) 274-3918</li>
        <li><span class="label">o:</span> (555) 806-2147</li>
      </ul>
      <p class="website"><strong>bayfieldcapitalworks</strong>.example</p>
    </div>
  </section>
</body>
</html>
```